Verpackungsdesign für Wellness- und Saunaprodukte
Zielgruppe
Kelvana ist ein junges Start-Up, das sich auf Wellness- und Saunaprodukte spezialisiert hat. Unsere Zielgruppe besteht zu beinahe gleichen Teilen aus männlichen und weiblichen Personen zwischen 30 und 60 Jahren. Unsere Produkte befinden sich eher im mittel- bis höherpreisigen Segment, daher streben wir ein hochwertiges Design für unsere Verpackungen an. Unsere Produktpalette reicht von Mentholkristallen, Saunaaufgüssen, bis hin zu Textilien für den Wellnessbereich und soll dementsprechend Menschen ansprechen, die sich einen gewissen Luxus im Alltag auch gönnen.
Aufgabenstellung
Inspiriert von der skandinavischen Sauna Kultur, möchten wir Momente der Erholung und
Entspannung in den Alltag unserer Kunden bringen. Die Geschichte des Saunierens ist eng mit der skandinavischen Kultur verbunden und skandinavische Stilelemente sind zeitgemäß und sprechen ein breites Publikum an. Das Design muss auf Dosen/Tiegel , Karton Verpackungen und Flaschen verschiedener Größen adaptierbar sein (siehe Bild im Anhang).
40g Tiegel(transparent) Höhe 40mm Durchmesser 60mm (ohne Deckel Silber gebürstet)
100g Tiegel(transparent) Höhe 53mm Durchmesser 71mm (ohne Deckel Silber gebürstet)
200g Tiegel(transparent) Höhe 65mm Durchmesser 90mm (ohne Deckel Silber gebürstet)
Karton Verpackung 124,5x49x49mm
Karton Verpackung 100x100x100mm
Flaschenetikett 134x67mm (Braunglas, schwarzer Deckel)
Es soll ein passendes Keyvisual erstellt werden.
Im Anhang sieht man die Verpackungen, Dosen, Flaschen sowie unsere ersten Design Entwürfe (an diese Anordnung der Elemente kann sich der Designer orientieren ). Das Logo bleibt wie gegeben. Das Produkt für die Tiegel soll Mentholkristalle sein.

```html
<!DOCTYPE html>
<html lang="de">
<head>
<meta charset="utf-8">
<title>Kelvana – Nordische Fichte Etikettvarianten</title>
<link href="https://fonts.googleapis.com/css2?family=Antonio:wght@100;300&family=Forum&family=Italiana&family=Montserrat:wght@300;400;800&family=Mrs+Saint+Delafield&family=Roboto+Condensed:wght@300&display=swap" rel="stylesheet">
<style>
  :root{
    --page:#ffffff;
    --paper:#f7f7f7;
    --band-grey:#d5d7d4;
    --band-sage:#d6e2de;
    --pine:#3a6f5c;
    --ink:#2c2c2c;
    --ink-soft:#555;
    --number:#d4d4d4;
    --emblem:#d4d6d3;
  }
  *{box-sizing:border-box;margin:0;padding:0}
  h1,h2{font-weight:400}
  html,body{width:1200px;height:2400px;overflow:hidden;background:var(--page)}
  body{position:relative;font-family:"Montserrat",sans-serif;color:var(--ink)}

  .variant-number{position:absolute;left:185px;width:70px;text-align:center;
    font-family:"Montserrat",sans-serif;font-weight:800;font-size:34px;letter-spacing:3px;color:var(--number)}

  .label{position:absolute;left:373px;width:483px;height:242px;background:var(--paper);overflow:hidden}
  .band-top{position:absolute;left:0;top:0;width:100%;height:15px;background:var(--band-grey)}
  .band-bottom{position:absolute;left:0;bottom:0;width:100%;height:27px;background:var(--band-sage)}

  .brand-tab{position:absolute;left:206px;top:0;width:71px;height:56px;background:var(--pine);
    display:flex;flex-direction:column;align-items:center;justify-content:center;gap:5px}
  .brand-dot{width:15px;height:15px;border-radius:50%;background:#fff}
  .brand-name{font-family:"Montserrat",sans-serif;font-weight:300;font-size:11px;color:#fff;letter-spacing:.3px}
  .sauna-tab{position:absolute;left:206px;bottom:0;width:71px;height:27px;background:var(--pine);
    display:flex;align-items:center;justify-content:center;color:#fff;font-size:7px;letter-spacing:.6px;white-space:nowrap}

  .info{position:absolute;top:40px;width:113px;text-align:center}
  .info--ingredients{left:25px}
  .info--usage{right:23px}
  .info-heading{font-size:10px;letter-spacing:1px;margin-bottom:10px;color:var(--ink);white-space:nowrap}
  .info-text{font-size:5.6px;line-height:1.35;color:var(--ink-soft);text-align:center;margin-bottom:13px}
  .volume{position:absolute;left:25px;top:178px;width:113px;text-align:center;font-size:13px;font-weight:400}

  .center{position:absolute;left:141px;top:70px;width:200px;text-align:center}
  .emblem{display:block;width:56px;height:56px;margin:0 auto 10px;border-radius:50%;background:var(--emblem)}
  .product-name{font-size:19px;line-height:1.1;letter-spacing:3px;color:var(--ink)}
  .rule{width:44px;height:1px;background:#999;margin:6px auto 7px}
  .product-type{font-size:7px;letter-spacing:2px;color:var(--ink-soft)}

  /* variant 01 – condensed */
  .v1 .info-heading,.v1 .product-name,.v1 .product-type,.v1 .sauna-tab{font-family:"Antonio",sans-serif;font-weight:100}
  .v1 .product-name{font-size:22px;letter-spacing:8px;line-height:1.15}
  .v1 .info-heading{font-size:12px;letter-spacing:2px}
  .v1 .product-type{font-size:8px;letter-spacing:3px}
  .v1 .sauna-tab{font-size:8px;letter-spacing:1px}
  .v1 .info-text{font-family:"Montserrat",sans-serif;font-weight:400;font-size:6px;letter-spacing:.7px;text-align:justify;text-align-last:center;margin-bottom:10px}

  /* variant 02 – fine display */
  .v2 .info-heading,.v2 .product-name,.v2 .product-type,.v2 .sauna-tab{font-family:"Italiana",serif}
  .v2 .info-heading{font-size:9px}
  .v2 .info-text,.v3 .info-text,.v4 .info-text{font-family:"Roboto Condensed",sans-serif;font-weight:300;font-size:5.5px;text-align:justify;text-align-last:center}

  /* variant 03 – script accents */
  .v3 .product-name,.v3 .sauna-tab{font-family:"Italiana",serif}
  .v3 .info-heading,.v3 .product-type{font-family:"Mrs Saint Delafield",cursive;letter-spacing:0;color:var(--ink)}
  .v3 .info{top:34px}
  .v3 .info-heading{font-size:20px;margin-bottom:4px}
  .v3 .product-type{font-size:15px}

  /* variant 04 – classic serif */
  .v4 .info-heading,.v4 .product-name,.v4 .product-type,.v4 .sauna-tab{font-family:"Forum",serif}
  .v4 .info-heading{font-size:10px}
  .v4 .product-name{font-size:22px;letter-spacing:2px}
</style>
</head>
<body>

<div class="variant-number" style="top:162px">01</div>
<section class="label v1" style="top:285px">
  <div class="band-top"></div><div class="band-bottom"></div>
  <div class="brand-tab"><span class="brand-dot"></span><span class="brand-name">Kelvana</span></div>
  <div class="sauna-tab">FÜR DIE SAUNA</div>
  <div class="info info--ingredients">
    <h2 class="info-heading">INHALTSSTOFFE</h2>
    <p class="info-text">Lorem ipsum dolor sit amet, consectetuer adipiscing elit, sed diam nonummy nibh euismod tincidunt ut laoreet dolore magna aliquam erat volutpat. Ut wisi enim ad</p>
    <p class="info-text">Lorem ipsum dolor sit amet, consectetuer adipiscing elit, sed diam nonummy nibh euismod</p>
  </div>
  <div class="volume">250 ml</div>
  <div class="center">
    <span class="emblem" role="img" aria-label="Nordisches Blüten-Ornament"></span>
    <h1 class="product-name">NORDISCHE<br>FICHTE</h1>
    <div class="rule"></div>
    <p class="product-type">AUFGUSS</p>
  </div>
  <div class="info info--usage">
    <h2 class="info-heading">ANWENDUNG</h2>
    <p class="info-text">Lorem ipsum dolor sit amet, consectetuer adipiscing elit, sed diam nonummy nibh euismod tincidunt ut laoreet dolore magna aliquam erat volutpat. Ut wisi enim ad</p>
    <p class="info-text">Lorem ipsum dolor sit amet, consectetuer adipiscing elit, sed diam nonummy nibh euismod</p>
    <p class="info-text">Lorem ipsum dolor sit amet, consectetuer adipiscing elit, sed diam nonummy nibh euismod</p>
  </div>
</section>

<div class="variant-number" style="top:689px">02</div>
<section class="label v2" style="top:813px">
  <div class="band-top"></div><div class="band-bottom"></div>
  <div class="brand-tab"><span class="brand-dot"></span><span class="brand-name">Kelvana</span></div>
  <div class="sauna-tab">FÜR DIE SAUNA</div>
  <div class="info info--ingredients">
    <h2 class="info-heading">INHALTSSTOFFE</h2>
    <p class="info-text">Lorem ipsum dolor sit amet, consectetuer adipiscing elit, sed diam nonummy nibh euismod tincidunt ut laoreet dolore magna aliquam erat volutpat. Ut wisi enim ad</p>
    <p class="info-text">Lorem ipsum dolor sit amet, consectetuer adipiscing elit, sed diam nonummy nibh euismod</p>
    <p class="info-text">Lorem ipsum dolor sit amet, consectetuer adipiscing elit, sed diam nonummy nibh euismod tincidunt ut laoreet dolore magna aliquam erat volutpat. Ut wisi enim ad</p>
  </div>
  <div class="volume">250 ml</div>
  <div class="center">
    <span class="emblem" role="img" aria-label="Nordisches Blüten-Ornament"></span>
    <h1 class="product-name">NORDISCHE<br>FICHTE</h1>
    <div class="rule"></div>
    <p class="product-type">AUFGUSS</p>
  </div>
  <div class="info info--usage">
    <h2 class="info-heading">ANWENDUNG</h2>
    <p class="info-text">Lorem ipsum dolor sit amet, consectetuer adipiscing elit, sed diam nonummy nibh euismod tincidunt ut laoreet dolore magna aliquam erat volutpat. Ut wisi enim ad</p>
    <p class="info-text">Lorem ipsum dolor sit amet, consectetuer adipiscing elit, sed diam nonummy nibh euismod</p>
    <p class="info-text">Lorem ipsum dolor sit amet, consectetuer adipiscing elit, sed diam nonummy nibh euismod tincidunt ut laoreet dolore magna aliquam erat volutpat. Ut wisi enim ad</p>
  </div>
</section>

<div class="variant-number" style="top:1218px">03</div>
<section class="label v3" style="top:1342px">
  <div class="band-top"></div><div class="band-bottom"></div>
  <div class="brand-tab"><span class="brand-dot"></span><span class="brand-name">Kelvana</span></div>
  <div class="sauna-tab">FÜR DIE SAUNA</div>
  <div class="info info--ingredients">
    <h2 class="info-heading">Inhaltsstoffe</h2>
    <p class="info-text">Lorem ipsum dolor sit amet, consectetuer adipiscing elit, sed diam nonummy nibh euismod tincidunt ut laoreet dolore magna aliquam erat volutpat. Ut wisi enim ad</p>
    <p class="info-text">Lorem ipsum dolor sit amet, consectetuer adipiscing elit, sed diam nonummy nibh euismod</p>
    <p class="info-text">Lorem ipsum dolor sit amet, consectetuer adipiscing elit, sed diam nonummy nibh euismod tincidunt ut laoreet dolore magna aliquam erat volutpat. Ut wisi enim ad</p>
  </div>
  <div class="volume">250 ml</div>
  <div class="center">
    <span class="emblem" role="img" aria-label="Nordisches Blüten-Ornament"></span>
    <h1 class="product-name">NORDISCHE<br>FICHTE</h1>
    <div class="rule"></div>
    <p class="product-type">Aufguss</p>
  </div>
  <div class="info info--usage">
    <h2 class="info-heading">Anwendung</h2>
    <p class="info-text">Lorem ipsum dolor sit amet, consectetuer adipiscing elit, sed diam nonummy nibh euismod tincidunt ut laoreet dolore magna aliquam erat volutpat. Ut wisi enim ad</p>
    <p class="info-text">Lorem ipsum dolor sit amet, consectetuer adipiscing elit, sed diam nonummy nibh euismod</p>
    <p class="info-text">Lorem ipsum dolor sit amet, consectetuer adipiscing elit, sed diam nonummy nibh euismod tincidunt ut laoreet dolore magna aliquam erat volutpat. Ut wisi enim ad</p>
  </div>
</section>

<div class="variant-number" style="top:1795px">04</div>
<section class="label v4" style="top:1920px">
  <div class="band-top"></div><div class="band-bottom"></div>
  <div class="brand-tab"><span class="brand-dot"></span><span class="brand-name">Kelvana</span></div>
  <div class="sauna-tab">FÜR DIE SAUNA</div>
  <div class="info info--ingredients">
    <h2 class="info-heading">INHALTSSTOFFE</h2>
    <p class="info-text">Lorem ipsum dolor sit amet, consectetuer adipiscing elit, sed diam nonummy nibh euismod tincidunt ut laoreet dolore magna aliquam erat volutpat. Ut wisi enim ad</p>
    <p class="info-text">Lorem ipsum dolor sit amet, consectetuer adipiscing elit, sed diam nonummy nibh euismod</p>
    <p class="info-text">Lorem ipsum dolor sit amet, consectetuer adipiscing elit, sed diam nonummy nibh euismod tincidunt ut laoreet dolore magna aliquam erat volutpat. Ut wisi enim ad</p>
  </div>
  <div class="volume">250 ml</div>
  <div class="center">
    <span class="emblem" role="img" aria-label="Nordisches Blüten-Ornament"></span>
    <h1 class="product-name">NORDISCHE<br>FICHTE</h1>
    <div class="rule"></div>
    <p class="product-type">AUFGUSS</p>
  </div>
  <div class="info info--usage">
    <h2 class="info-heading">ANWENDUNG</h2>
    <p class="info-text">Lorem ipsum dolor sit amet, consectetuer adipiscing elit, sed diam nonummy nibh euismod tincidunt ut laoreet dolore magna aliquam erat volutpat. Ut wisi enim ad</p>
    <p class="info-text">Lorem ipsum dolor sit amet, consectetuer adipiscing elit, sed diam nonummy nibh euismod</p>
    <p class="info-text">Lorem ipsum dolor sit amet, consectetuer adipiscing elit, sed diam nonummy nibh euismod tincidunt ut laoreet dolore magna aliquam erat volutpat. Ut wisi enim ad</p>
  </div>
</section>

</body>
</html>
```